Investor Presentation

We have a deck that is mostly finished that needs to be properly formatted and cleaned up. The presentation is for an investment in a financial firm. So the design we are looking for is very professional and minimalistic. A very clean look with conservative color schemes and fonts. The designer can leverage our existing logos, background, etc.

The final design files should have full editing functionality.

Target Market(s)

Sophisticated institutional investors

Industry/Entity Type

Conservative

Requirements
Nice to have
• Cleaned up / formatted tables from the attached files to add to the presentation.

```html
<!DOCTYPE html>
<html lang="en">
<head>
<meta charset="utf-8">
<title>Paragraph data Heading</title>
<link rel="stylesheet" href="https://fonts.googleapis.com/css2?family=Open+Sans:wght@400;600&family=Roboto:wght@400;500&display=swap">
<style>
  :root {
    --brand-teal: #007377;
    --heading-teal: #00797d;
    --footer-teal: #3795a0;
    --body-text: #454545;
    --white: #ffffff;
    --wash-light: rgba(224, 240, 242, 0.9);
    --wash-fade: rgba(224, 240, 242, 0);
  }
  * { box-sizing: border-box; margin: 0; padding: 0; }
  html, body { width: 1200px; height: 900px; overflow: hidden; background: var(--white); }
  .slide {
    position: relative;
    width: 1200px;
    height: 900px;
    overflow: hidden;
    background: var(--white);
    font-family: "Roboto", Arial, sans-serif;
  }
  .backdrop-wash {
    position: absolute;
    right: 0;
    top: 99px;
    width: 620px;
    height: 757px;
    background: radial-gradient(ellipse at 75% 55%, var(--wash-light) 0%, var(--wash-fade) 70%);
  }
  .slide-header {
    position: absolute;
    left: 0; top: 0;
    width: 1200px;
    height: 99px;
    background: var(--brand-teal);
  }
  .slide-title {
    position: absolute;
    left: 30px;
    top: 22px;
    font-family: "Open Sans", Arial, sans-serif;
    font-weight: 600;
    font-size: 41px;
    line-height: 50px;
    color: var(--white);
  }
  .company-mark {
    position: absolute;
    right: 16px;
    top: 44px;
    display: flex;
    align-items: center;
    gap: 10px;
    font-family: "Open Sans", Arial, sans-serif;
    font-weight: 400;
    font-size: 23px;
    color: var(--white);
  }
  .company-dot {
    width: 14px; height: 14px;
    border-radius: 50%;
    background: var(--white);
  }
  .content {
    position: absolute;
    left: 52px;
    top: 150px;
    width: 1100px;
  }
  .bullet-item { margin-bottom: 49px; }
  .bullet-title {
    display: flex;
    align-items: center;
    gap: 14px;
    font-weight: 500;
    font-size: 24px;
    line-height: 30px;
    color: var(--heading-teal);
  }
  .bullet-marker { flex: none; width: 32px; height: 32px; }
  .bullet-body {
    margin-left: 48px;
    margin-top: 8px;
    width: 1050px;
    font-size: 18px;
    line-height: 30px;
    color: var(--body-text);
  }
  .slide-footer {
    position: absolute;
    left: 0; bottom: 0;
    width: 1200px;
    height: 44px;
    background: var(--footer-teal);
    padding-left: 12px;
    font-family: "Open Sans", Arial, sans-serif;
    font-size: 19px;
    line-height: 44px;
    color: var(--white);
  }
</style>
</head>
<body>
<main class="slide">
  <div class="backdrop-wash" role="img" aria-label="Faint brand background decoration"></div>

  <header class="slide-header">
    <h1 class="slide-title">Paragraph data Heading</h1>
    <div class="company-mark"><span class="company-dot"></span>Calder Ridge Partners, LLC</div>
  </header>

  <section class="content">
    <article class="bullet-item">
      <h2 class="bullet-title">
        <svg class="bullet-marker" viewBox="0 0 32 32" aria-hidden="true"><rect x="9" y="9" width="14" height="14" fill="#2a9aa3"/></svg>
        Bullet Title Heading Here Bullet Title Heading Here
      </h2>
      <p class="bullet-body">Lorem ipsum dolor sit Lorem ipsum dolor sit&nbsp; Lorem ipsum dolor sit Lorem ipsum dolor sit&nbsp; Lorem ipsum dolor sit Lorem ipsum dolor sit&nbsp; Lorem ipsum dolor sit Lorem ipsum dolor sit&nbsp; Lorem ipsum dolor sit Lorem ipsum dolor sit&nbsp; Lorem ipsum dolor sit Lorem ipsum dolor sit&nbsp; Lorem ipsum dolor sit Lorem ipsum dolor sit&nbsp; Lorem ipsum dolor sit Lorem ipsum dolor sit</p>
    </article>

    <article class="bullet-item">
      <h2 class="bullet-title">
        <svg class="bullet-marker" viewBox="0 0 32 32" aria-hidden="true"><rect x="9" y="9" width="14" height="14" fill="#2a9aa3"/></svg>
        Bullet Title Heading Here Bullet Title Heading Here
      </h2>
      <p class="bullet-body">Lorem ipsum dolor sit Lorem ipsum dolor sit&nbsp; Lorem ipsum dolor sit Lorem ipsum dolor sit&nbsp; Lorem ipsum dolor sit Lorem ipsum dolor sit&nbsp; Lorem ipsum dolor sit Lorem ipsum dolor sit&nbsp; Lorem ipsum dolor sit Lorem ipsum dolor sit&nbsp; Lorem ipsum dolor sit Lorem ipsum dolor sit&nbsp; Lorem ipsum dolor sit Lorem ipsum dolor sit&nbsp; Lorem ipsum dolor sit Lorem ipsum dolor sit</p>
    </article>

    <article class="bullet-item">
      <h2 class="bullet-title">
        <svg class="bullet-marker" viewBox="0 0 32 32" aria-hidden="true"><rect x="9" y="9" width="14" height="14" fill="#2a9aa3"/></svg>
        Bullet Title Heading Here Bullet Title Heading Here
      </h2>
      <p class="bullet-body">Lorem ipsum dolor sit Lorem ipsum dolor sit&nbsp; Lorem ipsum dolor sit Lorem ipsum dolor sit&nbsp; Lorem ipsum dolor sit Lorem ipsum dolor sit&nbsp; Lorem ipsum dolor sit Lorem ipsum dolor sit&nbsp; Lorem ipsum dolor sit Lorem ipsum dolor sit&nbsp; Lorem ipsum dolor sit Lorem ipsum dolor sit&nbsp; Lorem ipsum dolor sit Lorem ipsum dolor sit&nbsp; Lorem ipsum dolor sit Lorem ipsum dolor sit</p>
    </article>
  </section>

  <footer class="slide-footer">Copyright text here</footer>
</main>
</body>
</html>
```